PTV Website

We need a completely new modern design for our website www.ptv.org.au.

The Keyholders Alliance League of Australia Inc is a non-profit, volunteer-run association representing owners of strata-titled residential developments. We provide education, information and lobbying to improve the management of apartment complexes and the lives of those living in them. We’re all about “owners helping owners”. More information on our organisation can be seen at www.ptv.org.au.

Our new logo (from a recent PixelHarbor contest) is attached.

Target Market(s)

Primary audience - Owners of residential apartments - both resident owners and investor owners
Secondary audiences – current and potential sponsors; organisations providing products & services to Owners Corporations & Body Corporates

Industry/Entity Type

Non-Profit

Number of Pages Required

3 pages

Requirements
Must have
• We need:
- A design for the home page
- A design for 2-column content pages
- Fonts and colours for
* standard text
* H1, H2, H3 and H4 heading tags
* Bulleted and numbered lists
- A complementary colour scheme for the Calendar page
- A complementary breadcrumb format
- A standard format to display the associated tags for any content page

The above are described in more detail in the attached document.

The design should:
- be modern, uncluttered and clean
- reflect a sense of community, coupled with authority, professionalism and knowledge
- be a fixed width of 1000px

At a minimum the files we need are:
- The source file (PSD with all component layers is preferred, but not mandatory)
- JPG preview files
- Any stand-alone images as a PNG with transparent backgrounds
- Details of all fonts and sizes used (if they can’t be easily identified in the source files)

Note: The site is built with the Drupal CMS, so all page elements must be able to be clearly isolated.
Should not have
• Any fonts that are not freely available

```html
<!DOCTYPE html>
<html lang="en">
<head>
<meta charset="utf-8">
<title>Keyholders Alliance League – Website Pages</title>
<link href="https://fonts.googleapis.com/css2?family=Arimo:wght@400;700&family=Noto+Sans:wght@400;700&display=swap" rel="stylesheet">
<style>
:root{
  --gold:#d69b2b;
  --gold-dark:#a9741a;
  --gold-light:#e8b552;
  --blue:#2149c4;
  --blue-bright:#1b52dc;
  --navy:#17308f;
  --link:#1d3fb3;
  --page-bg:#f3f3f3;
  --panel:#e8e8e8;
  --panel-line:#d2d2d2;
  --text:#3a3a3a;
  --white:#ffffff;
}
*{box-sizing:border-box;margin:0;padding:0}
html,body{width:1200px;height:4162px;overflow:hidden;background:var(--white)}
body{font-family:"Noto Sans",sans-serif;color:var(--text);position:relative}
.page{position:absolute;left:16px;width:1174px;background:var(--page-bg);border-left:1px solid #ddd;border-right:1px solid #ddd}
.divider{position:absolute;left:0;width:1200px;height:3px;background:#111}
.abs{position:absolute}

/* header */
.brand{position:absolute;left:24px;top:14px;display:flex;align-items:center;gap:20px}
.brand-square{width:112px;height:112px;background:var(--gold)}
.brand-name{font-family:"Arimo",sans-serif;font-weight:400;color:var(--navy);font-size:33px;line-height:31px;letter-spacing:3px}
.search{position:absolute;left:735px;top:40px;width:407px;height:97px;background:#ececec;border:1px solid #e2e2e2}
.search-field{position:absolute;left:11px;top:33px;width:283px;height:27px;background:var(--white);border:1px solid #ccc}
.search-btn{position:absolute;left:304px;top:33px;width:88px;height:27px;background:var(--blue);color:var(--white);font:400 19px "Arimo",sans-serif;text-align:center;line-height:27px}
.nav{position:absolute;left:8px;top:158px;width:1157px;height:68px;background:linear-gradient(#dfa93c,var(--gold) 60%,var(--gold-dark));border-bottom:3px solid var(--gold-dark)}
.nav a{position:absolute;top:0;line-height:64px;color:var(--white);font:400 23px "Arimo",sans-serif;text-decoration:none;text-shadow:0 1px 1px rgba(0,0,0,.25)}
.nav i{position:absolute;top:14px;width:1px;height:40px;background:rgba(255,255,255,.35)}
.crumbs{position:absolute;left:8px;top:234px;width:1157px;height:32px;background:#e6e6e6;font:700 12px "Noto Sans",sans-serif;color:var(--link);padding:8px 0 0 16px}
.crumbs .sep{display:inline-block;width:7px;height:7px;background:var(--gold);margin:0 4px 1px 10px}
.footer{position:absolute;left:8px;width:1157px;height:68px;background:linear-gradient(var(--gold-light),var(--gold) 50%,var(--gold-dark));color:var(--white);font:700 13px "Noto Sans",sans-serif;text-align:center;line-height:68px;letter-spacing:.5px}

/* shared blocks */
.heading{font:400 21px "Arimo",sans-serif;color:var(--link)}
.heading.big{font-size:28px}
.box{position:absolute;background:var(--panel);border:3px solid var(--panel-line)}
.topics{list-style:none;padding:16px 0 0 10px}
.topics li{font:700 12px "Noto Sans",sans-serif;color:#222;height:29px;display:flex;gap:9px}
.topics li::before{content:"";width:9px;height:9px;background:var(--blue);margin-top:4px;flex:none}
.dots{position:absolute;width:0;border-left:2px dotted #b9b9b9}
.copy{font-size:14px;line-height:17px;color:var(--text)}
.copy p{margin-bottom:17px}
.more{display:inline-block;background:var(--gold);border:1px solid var(--gold-dark);color:#222;font:700 11px "Noto Sans",sans-serif;padding:2px 5px}
.news-title{font:700 14px "Noto Sans",sans-serif;color:var(--link);text-decoration:underline;letter-spacing:.5px}
.news-meta{font:700 11px "Noto Sans",sans-serif;color:var(--link);margin:13px 0 14px}

/* hero */
.hero{position:absolute;left:8px;top:229px;width:791px;height:210px;background:linear-gradient(90deg,#173bb6,#0b2a9c);border-bottom:3px solid var(--gold);color:var(--white);padding:50px 0 0 21px;font-family:"Arimo",sans-serif}
.hero p{font-size:23px;line-height:40px;white-space:nowrap}
.hero b{font-weight:400;font-size:32px}
.hero-photo{position:absolute;left:805px;top:232px;width:360px;height:296px;background:linear-gradient(135deg,#c9d6e6,#5a6d86 45%,#1b2436 70%,#3b5fb5);border:4px solid var(--white);box-shadow:0 6px 10px rgba(0,0,0,.35);transform:rotate(2deg)}

/* login */
.label{font:700 13px "Noto Sans",sans-serif;color:#222;letter-spacing:.5px}
.field{width:218px;height:28px;background:var(--white);border:1px solid #ccc;margin:8px 0 22px}
.login-btn{display:inline-block;background:var(--blue);color:var(--white);font:400 16px "Arimo",sans-serif;padding:3px 12px;border:1px solid var(--navy)}

/* articles page */
.articles{list-style:none;position:absolute;left:32px;top:330px;width:330px}
.articles li{display:flex;gap:11px;font:700 12.5px "Noto Sans",sans-serif;color:var(--link);line-height:16px;margin-bottom:15px;letter-spacing:.7px}
.articles li::before{content:"";width:8px;height:8px;background:var(--gold);margin-top:4px;flex:none}
.article h2{font:400 19px "Noto Sans",sans-serif;color:var(--link);letter-spacing:1px;margin-bottom:8px}
.article{margin-bottom:38px}

/* calendar */
.views{position:absolute;top:322px;font:700 13px "Noto Sans",sans-serif;color:#222;display:flex;gap:30px;left:893px}
.cal-bar{position:absolute;left:24px;top:349px;width:1100px;height:40px;background:var(--blue);color:var(--white);font:700 13px "Noto Sans",sans-serif;line-height:40px;letter-spacing:1px}
.cal{position:absolute;left:24px;top:394px;width:1100px;border-collapse:collapse;table-layout:fixed}
.cal th{background:var(--gold);color:var(--white);font:700 13px "Noto Sans",sans-serif;height:31px;border-left:2px solid var(--white);letter-spacing:.5px}
.cal td{background:#e5e5e5;border:2px solid var(--white);vertical-align:top;text-align:right;padding:3px 4px}
.cal td span{display:inline-block;background:var(--blue);color:var(--white);font:700 13px "Noto Sans",sans-serif;min-width:26px;text-align:center;padding:1px 3px}
.popup{position:absolute;left:477px;top:833px;width:326px;height:223px;background:var(--blue-bright);border:3px solid var(--white);box-shadow:0 0 0 1px #9bb0e6;color:var(--white);font:700 12px "Noto Sans",sans-serif;line-height:15px;padding:14px 12px;letter-spacing:.5px}
.popup p{margin-bottom:14px}
.popup-badge{position:absolute;right:10px;top:44px;width:88px;height:72px;background:var(--white)}
.popup-close{position:absolute;right:8px;top:8px}
</style>
</head>
<body>

<!-- ================= HOME PAGE ================= -->
<section class="page" style="top:0;height:1373px">
  <header>
    <div class="brand"><div class="brand-square"></div><div class="brand-name">KEYHOLDERS<br>ALLIANCE<br>LEAGUE</div></div>
    <div class="search"><div class="search-field"></div><div class="search-btn">Search</div></div>
    <nav class="nav">
      <a style="left:28px">Home</a><i style="left:112px"></i>
      <a style="left:123px">About</a><i style="left:210px"></i>
      <a style="left:220px">News</a><i style="left:304px"></i>
      <a style="left:314px">Events</a><i style="left:410px"></i>
      <a style="left:420px">Membership</a><i style="left:576px"></i>
      <a style="left:586px">Sponsorship</a><i style="left:735px"></i>
      <a style="left:745px">Links</a><i style="left:825px"></i>
      <a style="left:835px">Contact</a><i style="left:941px"></i>
      <a style="left:951px">Members Only</a>
    </nav>
  </header>

  <div class="hero">
    <p><b>Owners</b> Helping Owners</p>
    <p><b>Representing</b> Strata Title Residential Developments</p>
    <p><b>Lobbying and Sharing</b> Information to Improve Apartment Living</p>
  </div>
  <div class="hero-photo" role="img" aria-label="Photo of a businessman in sunglasses in front of a curved high-rise apartment tower"></div>

  <!-- left column -->
  <h3 class="heading abs" style="left:21px;top:498px">Member Login</h3>
  <div class="box" style="left:21px;top:533px;width:263px;height:210px;padding:14px 0 0 14px">
    <div class="label">Username or e-mail: *</div><div class="field"></div>
    <div class="label">Password: *</div><div class="field" style="margin-bottom:10px"></div>
    <div class="login-btn">LOGIN</div>
    <div class="label" style="font-size:11px;margin-top:8px">Request new password</div>
  </div>
  <h3 class="heading abs" style="left:21px;top:778px">Topic List</h3>
  <div class="box" style="left:21px;top:811px;width:263px;height:190px">
    <ul class="topics"><li>Lorem ipsum.</li><li>Dolor sit amet, consectetur.</li><li>Adipisicing elit, sed do.</li><li>Eiusmod tempor incididunt ut et.</li><li>Dolore magna aliqua.</li><li>Ut enim ad &nbsp;veniam, nostrud.</li></ul>
  </div>
  <div class="dots" style="left:300px;top:500px;height:776px"></div>

  <!-- middle column -->
  <h1 class="heading big abs" style="left:315px;top:502px">Featured Announcements</h1>
  <div class="copy abs" style="left:315px;top:544px;width:520px">
    <p>What happens when complaints get trampled underfoot. When is a bylaw not a bylaw? When the Strata Disputes Review Panel decides it doesn't really matter.</p>
    <p>Government reintroduce clamping and towing of illegally parked cars to stop protracted legal and sometimes physical disputes they say are turning apartment car parks into battle grounds</p>
    <p style="text-align:right;font-weight:700;font-size:12px;text-decoration:underline;color:#222;padding-right:10px">Read More...</p>
  </div>
  <h2 class="heading big abs" style="left:315px;top:714px">Recent News</h2>
  <div class="abs" style="left:315px;top:759px;width:546px;height:481px;background:linear-gradient(#f8f8f8,#e6e6e6);border:1px solid #ddd;padding:30px 14px 0 13px">
    <div class="news-title">Bye bye to bylaws</div>
    <div class="news-meta">Submitted by admin on 9 December 2009</div>
    <p class="copy">What happens when complaints get trampled underfoot. When is a bylaw not a bylaw? When the Strata Disputes Review Panel decides it doesn't really matter, that's when</p>
    <div class="more" style="margin:14px 0 66px">More...</div>
    <div class="news-title">Push to clamp illegal parkers</div>
    <div class="news-meta">Submitted by admin on 9 December 2009</div>
    <p class="copy">RESIDENTS in flats and other strata buildings are demanding the State Government reintroduce clamping and towing of illegally parked cars to stop protracted legal and sometimes physical disputes they say are turning apartment car parks into battle grounds</p>
    <div class="more" style="margin-top:14px">More...</div>
  </div>
  <div class="dots" style="left:872px;top:500px;height:776px"></div>

  <!-- right column -->
  <h3 class="heading abs" style="left:885px;top:536px">Upcoming Events</h3>
  <div class="box copy" style="left:885px;top:568px;width:262px;height:186px;padding:18px 10px 0 10px;font-size:12.5px;line-height:15px">
    <p>Lorem ipsum dolor sit amet, ceius-mod tempor incididunt ut labore et.</p>
    <p>Dolore magna aliqua. Ut enim ad minim veniam, quis nostrud.</p>
    <p>ExDuis aute irure dolor in repre-henderit in voluptate.</p>
  </div>
  <h3 class="heading abs" style="left:885px;top:784px">Recent Forum Posts</h3>
  <div class="box copy" style="left:885px;top:819px;width:262px;height:187px;padding:16px 10px 0 10px;font-size:12.5px;line-height:15px">
    <p>Lorem ipsum dolor sit amet, consectetur adipisicincididunt ut labore et.</p>
    <p>Dolore magna aliqua. Ut enim ad minim veniam, quis nostrud.</p>
    <p>Exercitation ullamcoe dolor in reprehenderit in voluptate.</p>
  </div>

  <footer class="footer" style="top:1297px">©Keyholders Alliance League Inc 2008 | Disclaimer | Contact Us</footer>
</section>
<div class="divider" style="top:1437px"></div>

<!-- ================= CONTENT PAGE ================= -->
<section class="page" style="top:1442px;height:1308px">
  <header>
    <div class="brand"><div class="brand-square"></div><div class="brand-name">KEYHOLDERS<br>ALLIANCE<br>LEAGUE</div></div>
    <div class="search"><div class="search-field"></div><div class="search-btn">Search</div></div>
    <nav class="nav">
      <a style="left:28px">Home</a><i style="left:112px"></i>
      <a style="left:123px">About</a><i style="left:210px"></i>
      <a style="left:220px">News</a><i style="left:304px"></i>
      <a style="left:314px">Events</a><i style="left:410px"></i>
      <a style="left:420px">Membership</a><i style="left:576px"></i>
      <a style="left:586px">Sponsorship</a><i style="left:735px"></i>
      <a style="left:745px">Links</a><i style="left:825px"></i>
      <a style="left:835px">Contact</a><i style="left:941px"></i>
      <a style="left:951px">Members Only</a>
    </nav>
  </header>
  <div class="crumbs">Home<span class="sep"></span>Members Area</div>

  <h3 class="abs" style="left:24px;top:295px;font:700 17px 'Noto Sans',sans-serif;color:var(--link)">Articles</h3>
  <ul class="articles">
    <li>Building Managements Rights-<br>Buyers Beware</li>
    <li>Building Owners &amp; Occupiers-<br>How Up to date must they be (AS 1851)</li>
    <li>Deffects</li>
    <li>Demistifying High-Rise Fire Safety</li>
    <li>Executive Committees</li>
    <li>Fire Safety and the new standrds<br>( AS 1851-2005 )</li>
    <li>Insurance Tips For Stats Plan</li>
    <li>Noise</li>
    <li>Owners Corporation &amp; GST</li>
    <li>Serviced Appartments- A New Fom<br>Of Starta Abuse</li>
    <li>Smoke Alarms</li>
    <li>Strata Managers</li>
    <li>Which Way to Vote?<br>The Burden of Choice!</li>
  </ul>
  <h3 class="abs" style="left:24px;top:842px;font:700 16px 'Noto Sans',sans-serif;color:var(--link)">Topic List</h3>
  <div class="box" style="left:24px;top:872px;width:264px;height:189px">
    <ul class="topics"><li>Lorem ipsum.</li><li>Dolor sit amet, consectetur.</li><li>Adipisicing elit, sed do.</li><li>Eiusmod tempor incididunt ut et.</li><li>Dolore magna aliqua.</li><li>Ut enim ad &nbsp;veniam, nostrud.</li></ul>
  </div>
  <div class="dots" style="left:365px;top:294px;height:880px"></div>

  <main class="abs copy" style="left:388px;top:296px;width:760px">
    <article class="article">
      <h2>Building Managements Rights- Buyers Beware</h2>
      <p>The Keyholders Alliance League of Australia (PTV) is the peak body representing apartment owners, with most members drawn from Owners Corporations' Executive Committees (ECs) or con-cerned apartment owners around Australia. PTV is a not-for-profit association.</p>
      <p>Through representation, lobbying, information-sharing and networking, we perform a vital service for our members that supports them in living in and/or investing in strata titled property.</p>
      <p>We lobby for changes necessary to Government policy and legislation, and sit on many Government and industry boards and panels to present our views to those in power. The PTV gives members a voice at both State and Federal levels, and an opportunity to put forward their views on problems, solutions and the kind of future that, as apartment owners, we'd all like to see.</p>
    </article>
    <article class="article" style="margin-bottom:50px">
      <h2>Building Owners &amp; Occupiers- How Up to date must they be (AS 1851)</h2>
      <p>The PTV educates EC members and individuals by sharing experiences and disseminating informa-tion from relevant sources and related organisations.</p>
      <p>Regular meetings, seminars and an online discussion group give members access to fellow members' experiences in areas such as defects rectification, strata disputes, shared services, and levy management. These resources may save members thousands of dollars and an immense amount of heartache in the long run!</p>
    </article>
    <article class="article">
      <h2>Deffects</h2>
      <p>Regular meetings, seminars and an online discussion group give members access to fellow members' experiences in areas such as defects rectification, strata disputes, shared services, and levy management. These resources may save members thousands of dollars and an immense amount of heartache in the long run!</p>
    </article>
    <article class="article">
      <h2>Demistifying High-Rise Fire Safety</h2>
      <p>Regular meetings, seminars and an online discussion group give members access to fellow members' experiences in areas such as defects rectification, strata disputes, shared services, and levy management. These resources may save members thousands of dollars and an immense amount of heartache in the long run!</p>
    </article>
  </main>

  <footer class="footer" style="top:1223px">©Keyholders Alliance League Inc 2008 | Disclaimer | Contact Us</footer>
</section>
<div class="divider" style="top:2784px"></div>

<!-- ================= CALENDAR PAGE ================= -->
<section class="page" style="top:2789px;height:1316px">
  <header>
    <div class="brand"><div class="brand-square"></div><div class="brand-name">KEYHOLDERS<br>ALLIANCE<br>LEAGUE</div></div>
    <div class="search"><div class="search-field"></div><div class="search-btn">Search</div></div>
    <nav class="nav">
      <a style="left:28px">Home</a><i style="left:112px"></i>
      <a style="left:123px">About</a><i style="left:210px"></i>
      <a style="left:220px">News</a><i style="left:304px"></i>
      <a style="left:314px">Events</a><i style="left:410px"></i>
      <a style="left:420px">Membership</a><i style="left:576px"></i>
      <a style="left:586px">Sponsorship</a><i style="left:735px"></i>
      <a style="left:745px">Links</a><i style="left:825px"></i>
      <a style="left:835px">Contact</a><i style="left:941px"></i>
      <a style="left:951px">Members Only</a>
    </nav>
  </header>
  <div class="crumbs">Home<span class="sep"></span>Events</div>

  <h1 class="abs" style="left:23px;top:305px;font:400 19px 'Noto Sans',sans-serif;color:var(--link)">Events</h1>
  <div class="views"><span>Year</span><span>Month</span><span>Week</span><span>Day</span></div>
  <div class="cal-bar">
    <span style="position:absolute;left:12px">« Prev</span>
    <span style="position:absolute;left:0;width:100%;text-align:center">January 2010</span>
    <span style="position:absolute;right:22px">Next »</span>
  </div>
  <table class="cal">
    <colgroup><col style="width:23px"><col style="width:137px"><col style="width:142px"><col style="width:144px"><col style="width:176px"><col style="width:163px"><col style="width:134px"><col style="width:181px"></colgroup>
    <thead><tr><th></th><th>Sunday</th><th>Monday</th><th>Tuesday</th><th>Wednesday</th><th>Thursday</th><th>Friday</th><th>Saturday</th></tr></thead>
    <tbody>
      <tr style="height:82px"><td></td><td></td><td></td><td></td><td></td><td></td><td><span>1</span></td><td><span>2</span></td></tr>
      <tr style="height:100px"><td></td><td><span>3</span></td><td><span>4</span></td><td><span>5</span></td><td><span>6</span></td><td><span>7</span></td><td><span>8</span></td><td><span>9</span></td></tr>
      <tr style="height:91px"><td></td><td><span>10</span></td><td><span>11</span></td><td><span>12</span></td><td><span>13</span></td><td><span>14</span></td><td><span>15</span></td><td><span>16</span></td></tr>
      <tr style="height:95px"><td></td><td><span>17</span></td><td><span>18</span></td><td><span>19</span></td><td><span>20</span></td><td><span>21</span></td><td><span>22</span></td><td><span>23</span></td></tr>
      <tr style="height:100px"><td></td><td><span>24</span></td><td><span>25</span></td><td><span>26</span></td><td><span>27</span></td><td><span>28</span></td><td><span>29</span></td><td><span>30</span></td></tr>
      <tr style="height:97px"><td></td><td><span>31</span></td><td></td><td></td><td></td><td></td><td></td><td></td></tr>
    </tbody>
  </table>

  <aside class="popup">
    <svg class="popup-close" width="16" height="16" viewBox="0 0 16 16" aria-hidden="true"><path d="M3 3 L13 13 M13 3 L3 13" stroke="#fff" stroke-width="3"/></svg>
    <p>SPG Consumer Awareness Seminar</p>
    <p>Time: &nbsp;24 February 2010<br>6:15pm - 7:45pm</p>
    <p>Location:<br>Bayside Event Centre<br>145 Carrow Street</p>
    <p>Sydney<br>Organiser: &nbsp;Strata Practice<br>Guild</p>
    <div class="popup-badge"></div>
  </aside>

  <footer class="footer" style="top:1224px">©Keyholders Alliance League Inc 2008 | Disclaimer | Contact Us</footer>
</section>
<div class="divider" style="top:4157px"></div>

</body>
</html>
```